Business card design needed

I would like a one sided black business card with the information provided above. Refer to my website www.brightvolleyracquets.com.au for an example of colors I have used for my site, would like to keep this consistent for my business cards also, I will upload my logo below.

I am a new small business that provides tennis customers with racquet re stringing, tennis strings and accessories.

Industry/Entity Type

Small Business

Contact Information for Business Card

Bright Volley Tennis

Owen Whitby
Managing Director

brightvolleyracquets@mailbox.example
www.brightvolleyracquets.com.au
0491 726 305

Racquet Restringing/Tennis Strings/Accessories

Requirements
Must have
• Must have my logo and card must be black

```html
<!DOCTYPE html>
<html lang="en">
<head>
<meta charset="utf-8">
<title>Bright Volley Tennis – Business Card</title>
<link rel="stylesheet" href="https://fonts.googleapis.com/css2?family=Arimo:wght@400;700&display=swap">
<style>
  :root {
    --stage: #e9e6e1;
    --card-black: #000000;
    --brand-green: #b5d334;
    --brand-blue: #1f4b85;
    --text-white: #ffffff;
    --text-soft: #e6e6e6;
    --divider: #bfbfbf;
  }
  * { box-sizing: border-box; margin: 0; padding: 0; }
  html, body {
    width: 1200px; height: 475px; overflow: hidden;
    background: var(--stage);
    font-family: "Arimo", Arial, sans-serif;
  }
  .canvas { position: relative; width: 1200px; height: 475px; }

  .card {
    position: absolute;
    width: 547px; height: 313px;
    background: var(--card-black);
    border-radius: 20px;
    overflow: hidden;
  }
  .card--front { left: 27px; top: 81px; }
  .card--back  { left: 607px; top: 86px; }

  .brand {
    position: absolute; left: 0; right: 0;
    display: flex; flex-direction: column; align-items: center; gap: 10px;
  }
  .card--front .brand { top: 48px; }
  .card--back .brand  { top: 72px; }
  .brand__mark {
    width: 44px; height: 44px; border-radius: 50%;
    background: var(--brand-green);
  }
  .brand__name {
    color: var(--brand-green);
    font-weight: 700; font-size: 34px; letter-spacing: 0.5px;
    white-space: nowrap;
  }

  .contact-name {
    position: absolute; left: 85px; top: 188px;
    color: var(--brand-green);
  }
  .contact-name__person { font-size: 19px; letter-spacing: 0.6px; text-transform: uppercase; }
  .contact-name__role { font-size: 14px; margin-top: 3px; }

  .contact-divider {
    position: absolute; left: 252px; top: 190px;
    width: 1px; height: 42px; background: var(--divider);
  }
  .contact-details {
    position: absolute; left: 271px; top: 188px;
    color: var(--text-soft); font-size: 14.5px; line-height: 20px; letter-spacing: 0.3px;
  }

  .footer-band { position: absolute; left: 0; bottom: 0; width: 547px; height: 48px; }
  .footer-url {
    position: absolute; left: 279px; bottom: 12px;
    color: var(--text-white); font-size: 14px; letter-spacing: 0.3px;
  }

  .site-url {
    position: absolute; left: 0; right: 0; top: 237px;
    text-align: center; color: var(--text-white);
    font-size: 13.5px; letter-spacing: 2.2px;
  }
</style>
</head>
<body>
<main class="canvas">

  <section class="card card--front" aria-label="Business card front">
    <div class="brand">
      <span class="brand__mark" aria-hidden="true"></span>
      <span class="brand__name">Bright Volley Tennis</span>
    </div>

    <div class="contact-name">
      <p class="contact-name__person">Owen Whitby</p>
      <p class="contact-name__role">Managing Director</p>
    </div>
    <div class="contact-divider" aria-hidden="true"></div>
    <div class="contact-details">
      <p>P : 0491 726 305</p>
      <p>E : brightvolleyracquets@mailbox.example</p>
    </div>

    <svg class="footer-band" viewBox="0 0 547 48" aria-hidden="true">
      <rect x="0" y="0" width="547" height="48" fill="var(--brand-blue)"/>
      <polygon points="0,0 255,0 236,19 0,19" fill="var(--card-black)"/>
      <polygon points="0,4 247,4 236,17 0,17" fill="var(--brand-green)"/>
      <polygon points="0,19 236,19 230,25 0,25" fill="var(--card-black)"/>
    </svg>
    <p class="footer-url">www.brightvolleyracquets.com.au</p>
  </section>

  <section class="card card--back" aria-label="Business card back">
    <div class="brand">
      <span class="brand__mark" aria-hidden="true"></span>
      <span class="brand__name">Bright Volley Tennis</span>
    </div>
    <p class="site-url">www.brightvolleyracquets.com.au</p>
  </section>

</main>
</body>
</html>
```